Super elegant, crisp & clean Business card design required

We recently upgraded our branding - which is on our website - talvendoraphoto.com

I would like a simple, yet elegant, clean business card design please.

The font of my logo is Cinzel - and because of the natural colour - it's best to have this on a black background.

I would like to have the back of the business card - with simply my logo.

PLEASE DO NOT SUBMIT A COMPLICATED / UNCLEAN DESIGN

Industry/Entity Type

Business

Contact Information for Business Card

Talven Doroshko Photography

Font styles to use
Other font styles liked:
• Cinzel

Requirements
Must have
• A backpage with nothing but my logo
• Simple design - stands out
Should not have
• Colour that dont align with my logo
• Over complicated '/ non symmetrical design

```html
<!DOCTYPE html>
<html lang="en">
<head>
<meta charset="utf-8">
<title>Talven Doroshko Photography – Business Card</title>
<link rel="stylesheet" href="https://fonts.googleapis.com/css2?family=Cinzel:wght@400&family=Open+Sans:wght@400;700&display=swap">
<style>
  :root {
    --backdrop: #ebebeb;
    --card-black: #111111;
    --card-white: #ffffff;
    --gold: #a8977a;
    --ink: #4a4a4a;
    --ink-soft: #6b6b6b;
  }
  * { box-sizing: border-box; margin: 0; padding: 0; }
  html, body {
    width: 1200px;
    height: 1006px;
    overflow: hidden;
    background: var(--backdrop);
  }
  .sheet {
    width: 1200px;
    height: 1006px;
    display: flex;
    flex-direction: column;
    align-items: center;
    justify-content: center;
    gap: 70px;
  }
  .card {
    width: 560px;
    height: 320px;
    position: relative;
    box-shadow: 0 6px 18px rgba(0, 0, 0, 0.12);
  }

  /* Back of card: brand lockup only */
  .card--back {
    background: var(--card-black);
    display: flex;
    align-items: center;
    justify-content: center;
    gap: 28px;
  }
  .brand {
    font-family: "Cinzel", serif;
    font-weight: 400;
    color: var(--gold);
    text-align: center;
    line-height: 1;
  }
  .card--back .brand__name { font-size: 26px; letter-spacing: 1px; }
  .card--back .brand__line { font-size: 12px; letter-spacing: 9px; margin-top: 10px; }
  .brand-square {
    border: 1.5px solid var(--gold);
    flex: none;
  }
  .card--back .brand-square { width: 108px; height: 108px; }

  /* Front of card: contact details */
  .card--front { background: var(--card-white); }
  .card--front .lockup {
    position: absolute;
    top: 44px;
    right: 44px;
    display: flex;
    align-items: center;
    gap: 10px;
  }
  .card--front .brand__name { font-size: 12px; letter-spacing: 0.5px; }
  .card--front .brand__line { font-size: 6px; letter-spacing: 4px; margin-top: 5px; }
  .card--front .brand-square { width: 44px; height: 44px; border-width: 1px; }

  .contact {
    position: absolute;
    left: 44px;
    bottom: 44px;
    font-family: "Open Sans", sans-serif;
    color: var(--ink);
  }
  .contact__name {
    font-size: 17px;
    font-weight: 700;
    letter-spacing: 0.5px;
    text-transform: uppercase;
  }
  .contact__role {
    font-size: 11px;
    color: var(--ink-soft);
    margin-bottom: 14px;
  }
  .contact__phone { font-size: 15px; margin-bottom: 6px; }
  .contact__detail { font-size: 10px; color: var(--ink-soft); line-height: 1.5; }
  .contact__web { text-transform: uppercase; letter-spacing: 0.3px; }
</style>
</head>
<body>
<main class="sheet">
  <section class="card card--back" aria-label="Card back">
    <div class="brand">
      <div class="brand__name">Talven Doroshko</div>
      <div class="brand__line">Photography</div>
    </div>
    <div class="brand-square"></div>
  </section>

  <section class="card card--front" aria-label="Card front">
    <div class="lockup">
      <div class="brand">
        <div class="brand__name">Talven Doroshko</div>
        <div class="brand__line">Photography</div>
      </div>
      <div class="brand-square"></div>
    </div>
    <div class="contact">
      <div class="contact__name">Orin Haldane</div>
      <div class="contact__role">Photographer</div>
      <div class="contact__phone">123 456 789</div>
      <div class="contact__detail">lorem@ipsum.com</div>
      <div class="contact__detail contact__web">talvendoraphoto.com</div>
    </div>
  </section>
</main>
</body>
</html>
```